Start-Up für Training, Coaching & Consulting sucht modernes Webdesign!
Zielgruppe
Wer ist TAVI Training, Coaching & Consulting?
Wir führen Führungskräftetrainings durch, machen Privatkunden für Bewerbungen fit und unterstützen Unternehmen mit Verkaufstrainings. Wir entwickeln Persönlichkeiten im Coaching. Wir beraten Unternehmen und helfen ihnen dabei, ihre Geschäftsabläufe und Prozesse zu optimieren. Dabei steht unsere hohe Qualität im Mittelpunkt - gemeinsam mit unseren kreativen Trainingsmethoden. Unser Background (Diplom-Kaufleute und geprüfte Trainer) bietet dafür die passende Ausgangslage.
Was bedeutet TAVI?
Tavi ist Maori und bdeutet Kreis/Spirale. Er symbolisiert einen wachsenden Silberfarn und steht für persönliche Entwicklung und Entfaltung. Der Tavi ist einerseits unser Namensgeber und unser Logo, andererseits steht der Tavi aber auch für unsere Werte: Denn wir wollen unseren Kunden dabei helfen zu wachsen und sich weiterzuentwickeln - und dies auf eine hochqualitative und seriöse Art und Weise ohne den Eindruck von Esoterik oder Erlebnispädagogik zu vermitteln.
Aufgabenstellung
Modernes Design, das unsere Philosophie widerspiegelt: Wir möchten unseren Kunden auf seriöse und hochqualitative Weise weiterentwickeln. Wir stehen für nachhaltigen Lernerfolg, kreative Trainingsmethoden, Abwechslung, Spaß am Lernen, Qualität, Kompetenz, Fachwissen und Dynamik.
Layout:
1) Header: QMSR geprüfter Trainer, Menüpunkte (siehe Architektur)
2) Banner
3) 3 Teaser (Training, Coaching, Consulting) + Header + 2-3 Zeilen Text (+Icons)
>>> Sichtbarer Bereich auf Homepage: Menü, Banner, Teaser
4) "Warum Sie uns wählen sollten": 5 bullet points ohne weiteren Text
5) "Aus unserem Blog": Frame für 3 Blogartikel + Bild + Datum + Header + 2-3 Zeilen Text
6) Alle drei QMSR Logos
7) Footer: Click Us (quick links), Contact Us (Adresse), Follow Us (Pinnwald, ZOLP, Kontaktor)
8) Copyright + Impressum
>>> Das Design soll klar sein, aber nicht zu kantig. Vielmehr sollen abgerundete Ecken und dynamische Elemente genutzt werden.
Architektur:
3 Ebenen:
1) Homepage
2) TAVI, Training, Coaching, Consulting, für Trainer, Kundenstimmen/Referenzen, Kontakt
3) noch zu bestimmende Produktdetailseiten
Texte werden noch erstellt, Layout kann ggf. mit Platzhaltertext gefüllt werden.
Bildmaterial: Logo und vorhandenes Imagebild werden zur Verfügung gestellt. Bilder können ggf. gekauft werden. Vorschläge erwünscht.
Corporate colors:
grün: #a2c61b + monochromatic colors
http://www.tintoskop.de/a2c61b
grau: #474747 + monochromatic colors
http://www.tintoskop.de/474747

```html
<!DOCTYPE html>
<html lang="de">
<head>
<meta charset="utf-8">
<title>TAVI Training, Coaching & Consulting</title>
<link href="https://fonts.googleapis.com/css2?family=Open+Sans:wght@400;600;700&family=Ubuntu:wght@400;500&display=swap" rel="stylesheet">
<style>
:root{
  --green:#a2c61b;
  --green-light:#c5dd62;
  --grey:#474747;
  --dark:#2b2b2b;
  --text:#222;
  --muted:#777;
  --badge:#1d5fb0;
  --white:#fff;
}
*{box-sizing:border-box;margin:0;padding:0}
html,body{width:885px;height:1200px;overflow:hidden;background:var(--white);font-family:'Open Sans',sans-serif;color:var(--text)}
.page{position:relative;width:885px;height:1200px}
.abs{position:absolute}

/* header */
.brand{left:27px;top:10px;display:flex;align-items:center;gap:6px}
.brand-dot{width:26px;height:26px;border-radius:50%;background:var(--green)}
.brand-name{font-weight:700;font-size:27px;color:var(--grey);line-height:1}
.brand-tag{left:27px;top:45px;font-size:6px;color:var(--grey)}
.cert-badge{left:202px;top:17px;width:84px;height:24px;background:var(--badge);border-radius:2px}
.nav{top:22px;font-weight:700;font-size:12px;color:var(--dark);display:flex;align-items:center;gap:3px}
.nav.active{color:var(--green)}
.rule{left:0;width:885px;height:6px;background:linear-gradient(90deg,var(--green-light),var(--green))}

/* hero */
.hero{left:0;top:64px;width:885px;height:235px;background:radial-gradient(ellipse at 55% 40%,#7cc23a 0%,#3f8a1e 35%,#173f10 70%,#0b1f08 100%)}
.hero-title{left:189px;top:163px;font-family:'Ubuntu',sans-serif;font-size:20px;line-height:23px;color:var(--white)}
.hero-btn{left:190px;top:243px;width:94px;height:30px;border-radius:15px;background:var(--green);font-weight:700;font-size:7.5px;color:var(--dark);display:flex;align-items:center;justify-content:center}
.hero-arrow{top:164px;width:34px;height:34px;border-radius:50%;background:var(--green);display:flex;align-items:center;justify-content:center}

/* teasers */
.teaser-img{width:136px;height:136px;border-radius:50%;top:323px}
.teaser-bar{left:0;top:476px;width:885px;height:27px;background:var(--dark)}
.teaser-title{top:480px;font-weight:700;font-size:13px;color:var(--green);width:200px;text-align:center}
.teaser-card{top:503px;height:83px;background:var(--white);border-radius:0 0 8px 8px;box-shadow:0 1px 5px rgba(0,0,0,.22);padding:12px 20px;font-size:8.6px;line-height:14px}

/* reasons */
.section-title{font-weight:600;font-size:20px;color:var(--dark)}
.reason-num{left:93px;width:34px;height:34px;border-radius:50%;background:var(--green);font-weight:700;font-size:11px;display:flex;align-items:center;justify-content:center;color:var(--dark)}
.reason-text{left:144px;font-size:16.5px;color:var(--green)}

/* news */
.news-img{left:492px;width:80px;height:80px;border-radius:50%}
.news-date{left:610px;font-size:8px;color:var(--dark)}
.news-head{left:610px;font-size:13px;color:var(--green)}
.news-body{left:610px;width:190px;font-size:7.5px;line-height:11px;color:var(--muted)}
.news-more{left:610px;font-size:7.5px;font-weight:700;color:var(--green);display:flex;align-items:center;gap:3px}

/* partner badges */
.partner{top:1007px;height:24px;background:var(--badge);border-radius:2px}

/* footer */
.footer{left:0;top:1081px;width:885px;height:119px;background:var(--dark)}
.f-head{top:1100px;font-weight:600;font-size:13px;color:var(--green)}
.f-list{top:1129px;font-size:10px;line-height:13px;color:var(--white);list-style:none}
.f-list li{display:flex;align-items:center;gap:6px}
.f-ico{width:8px;height:8px;background:var(--white);border-radius:1px}
.f-brand{left:93px;top:1104px;display:flex;align-items:center;gap:5px}
</style>
</head>
<body>
<div class="page">

  <!-- header -->
  <div class="abs brand"><span class="brand-dot"></span><span class="brand-name">TAVI</span></div>
  <div class="abs brand-tag">Training · Coaching · Consulting</div>
  <div class="abs cert-badge" role="img" aria-label="Zertifikatsabzeichen"></div>
  <div class="abs nav active" style="left:383px">LEISTUNGEN
    <svg width="9" height="9" viewBox="0 0 10 10"><circle cx="5" cy="5" r="5" fill="#a2c61b"/><path d="M2.8 4l2.2 2.2L7.2 4" stroke="#2b2b2b" stroke-width="1.4" fill="none"/></svg></div>
  <div class="abs nav" style="left:493px">ÜBER UNS</div>
  <div class="abs nav" style="left:580px">FÜR TRAINER
    <svg width="8" height="8" viewBox="0 0 10 10"><path d="M2 3.5l3 3 3-3" stroke="#2b2b2b" stroke-width="1.8" fill="none"/></svg></div>
  <div class="abs nav" style="left:695px">REFERENZEN</div>
  <div class="abs nav" style="left:799px">KONTAKT</div>
  <div class="abs rule" style="top:59px"></div>

  <!-- hero -->
  <div class="abs hero" role="img" aria-label="Nahaufnahme eines sich entrollenden Farnblatts"></div>
  <div class="abs hero-arrow" style="left:27px"><svg width="16" height="16" viewBox="0 0 16 16"><path d="M10 2L4 8l6 6" stroke="#2b2b2b" stroke-width="3" fill="none"/></svg></div>
  <div class="abs hero-arrow" style="left:822px"><svg width="16" height="16" viewBox="0 0 16 16"><path d="M6 2l6 6-6 6" stroke="#2b2b2b" stroke-width="3" fill="none"/></svg></div>
  <div class="abs hero-title">Lernen und Wissen<br>vermitteln:<br>Leicht gemacht</div>
  <div class="abs hero-btn">MEHR ERFAHREN</div>
  <div class="abs rule" style="top:299px"></div>

  <!-- teasers -->
  <div class="abs teaser-img" style="left:96px;background:linear-gradient(180deg,#3f7fb0 0%,#d9a36a 50%,#5b5548 75%,#2f2f33 100%)" role="img" aria-label="Läufer auf einer Küstenstraße im Abendlicht"></div>
  <div class="abs teaser-img" style="left:373px;background:radial-gradient(circle,#9fd45a 0%,#4d9a2a 50%,#1e4d14 100%)" role="img" aria-label="Sich entrollender Farn"></div>
  <div class="abs teaser-img" style="left:650px;background:linear-gradient(180deg,#e4e4e8 0%,#a8a6a6 50%,#3c3a38 80%,#2a2928 100%)" role="img" aria-label="Person sitzt auf einem Felsvorsprung"></div>
  <div class="abs teaser-bar"></div>
  <div class="abs teaser-title" style="left:61px">TRAINING</div>
  <div class="abs teaser-title" style="left:342px">COACHING</div>
  <div class="abs teaser-title" style="left:616px">CONSULTING</div>
  <div class="abs teaser-card" style="left:36px;width:258px">Durch mich gebiert das Netz die Kunst aus sich selbst heraus. Nicht schlicht reproduktiver Natur, repräsentiere ich vielmehr die kontinuierliche Evolution des Wortes.</div>
  <div class="abs teaser-card" style="left:314px;width:258px">Durch mich gebiert das Netz die Kunst aus sich selbst heraus. Nicht schlicht reproduktiver Natur, repräsentiere ich vielmehr die kontinuierliche Evolution des Wortes.</div>
  <div class="abs teaser-card" style="left:590px;width:258px">Durch mich gebiert das Netz die Kunst aus sich selbst heraus. Nicht schlicht reproduktiver Natur, repräsentiere ich vielmehr die kontinuierliche Evolution des Wortes.</div>

  <!-- reasons -->
  <div class="abs section-title" style="left:93px;top:622px">Warum Sie uns wählen sollten</div>
  <div class="abs reason-num" style="top:670px">1</div><div class="abs reason-text" style="top:674px">Grund Nummer Eins</div>
  <div class="abs reason-num" style="top:733px">2</div><div class="abs reason-text" style="top:738px">Grund Nummer Zwei</div>
  <div class="abs reason-num" style="top:798px">3</div><div class="abs reason-text" style="top:802px">Grund Nummer Drei</div>
  <div class="abs reason-num" style="top:864px">4</div><div class="abs reason-text" style="top:868px">Grund Nummer Vier</div>
  <div class="abs reason-num" style="top:929px">5</div><div class="abs reason-text" style="top:933px">Grund Nummer Fünf</div>

  <!-- news -->
  <div class="abs section-title" style="left:609px;top:622px">News</div>

  <div class="abs news-img" style="top:670px;background:linear-gradient(180deg,#3f7fb0 0%,#d9a36a 50%,#3a3a3c 100%)" role="img" aria-label="Küstenstraße im Abendlicht"></div>
  <div class="abs news-date" style="top:668px">02.02.2016</div>
  <div class="abs news-head" style="top:679px">Heading 01</div>
  <div class="abs news-body" style="top:697px">Durch mich gebiert das Netz die Kunst aus sich selbst heraus. Nicht schlicht reproduktiver Natur, repräsentiere ich vielmehr die kontinuierliche Evolution des Wortes.</div>
  <div class="abs news-more" style="top:741px">mehr <svg width="7" height="7" viewBox="0 0 10 10"><circle cx="5" cy="5" r="5" fill="#a2c61b"/><path d="M4 2.8L6.2 5 4 7.2" stroke="#2b2b2b" stroke-width="1.5" fill="none"/></svg></div>

  <div class="abs news-img" style="top:779px;background:radial-gradient(circle,#9fd45a 0%,#4d9a2a 50%,#1e4d14 100%)" role="img" aria-label="Sich entrollender Farn"></div>
  <div class="abs news-date" style="top:777px">09.02.2016</div>
  <div class="abs news-head" style="top:788px">Heading 02</div>
  <div class="abs news-body" style="top:806px">Durch mich gebiert das Netz die Kunst aus sich selbst heraus. Nicht schlicht reproduktiver Natur, repräsentiere ich vielmehr die kontinuierliche Evolution des Wortes.</div>
  <div class="abs news-more" style="top:850px">mehr <svg width="7" height="7" viewBox="0 0 10 10"><circle cx="5" cy="5" r="5" fill="#a2c61b"/><path d="M4 2.8L6.2 5 4 7.2" stroke="#2b2b2b" stroke-width="1.5" fill="none"/></svg></div>

  <div class="abs news-img" style="top:885px;background:linear-gradient(180deg,#e4e4e8 0%,#a8a6a6 50%,#2f2e2c 100%)" role="img" aria-label="Person auf einem Felsvorsprung"></div>
  <div class="abs news-date" style="top:883px">14.02.2016</div>
  <div class="abs news-head" style="top:894px">Heading 03</div>
  <div class="abs news-body" style="top:912px">Durch mich gebiert das Netz die Kunst aus sich selbst heraus. Nicht schlicht reproduktiver Natur, repräsentiere ich vielmehr die kontinuierliche Evolution des Wortes.</div>
  <div class="abs news-more" style="top:956px">mehr <svg width="7" height="7" viewBox="0 0 10 10"><circle cx="5" cy="5" r="5" fill="#a2c61b"/><path d="M4 2.8L6.2 5 4 7.2" stroke="#2b2b2b" stroke-width="1.5" fill="none"/></svg></div>

  <!-- partner badges -->
  <div class="abs partner" style="left:329px;width:18px" role="img" aria-label="Mitgliedsabzeichen"></div>
  <div class="abs partner" style="left:389px;width:18px" role="img" aria-label="Verbandsabzeichen"></div>
  <div class="abs partner" style="left:462px;width:88px" role="img" aria-label="Zertifikatsabzeichen"></div>

  <!-- footer -->
  <div class="abs rule" style="top:1075px"></div>
  <div class="abs footer"></div>
  <div class="abs f-brand"><span class="brand-dot" style="width:22px;height:22px"></span><span class="brand-name" style="color:#fff;font-size:25px">TAVI</span></div>
  <div class="abs brand-tag" style="left:93px;top:1140px;color:#fff">Training · Coaching · Consulting</div>

  <div class="abs f-head" style="left:249px">Click Us</div>
  <ul class="abs f-list" style="left:249px"><li>Link Title Number 1</li><li>Link Title Number 2</li><li>Link Title Number 3</li></ul>

  <div class="abs f-head" style="left:414px">Contact Us</div>
  <ul class="abs f-list" style="left:414px"><li>Link Title Number 1</li><li>Link Title Number 2</li><li>Link Title Number 3</li></ul>

  <div class="abs f-head" style="left:585px">Follow Us</div>
  <ul class="abs f-list" style="left:585px">
    <li><span class="f-ico"></span>Pinnwald</li>
    <li><span class="f-ico"></span>Zwitscha</li>
    <li><span class="f-ico"></span>ZOLP</li>
    <li><span class="f-ico"></span>Bildfluss</li>
  </ul>

  <div class="abs f-head" style="left:719px">Impressum</div>
  <ul class="abs f-list" style="left:719px"><li>© 2016 TAVI</li></ul>
</div>
</body>
</html>
```